A start-up named "lumerova" - a clinical research organization needs a new PowerPoint design

We need a new PowerPoint Design (incl. business card and stationery design) for an early-stage start-up named "lumerova" seeking to build an ecosystem/ strategic partner alliances or consortium of committed and active collaborators to guide important components of the clinical trial.

Our ultimate goal is to avoid false neutrals – therapies that have not been and may never be evaluated in clinical trials due to the costs and/ or complexity.

The final design should highlight our patient-centric approach, innovative study design supported with the novel AI platform to make a stronger impact on patient lives.

Please see the attached brief for more details.
Updates

Requesting the proposals on color-coding, business-card designs, clinical research visuals, and icons as well as stationery design.

Target Market(s)

Pharma/ Biotech Executives
Medical Institutions
Clinical Trial Participants (Patients)

Colors
e34398

Requirements
Must have
• Use the Color Version of purple/ magenta logo

```html
<!DOCTYPE html>
<html lang="en">
<head>
<meta charset="utf-8">
<title>Lumerova – Stationery &amp; Business Card Design</title>
<link rel="stylesheet" href="https://fonts.googleapis.com/css2?family=Ubuntu:wght@400;500;700&family=Open+Sans:wght@300&display=swap">
<style>
  :root {
    --board: #e6e6e6;
    --paper: #f4f4f4;
    --white: #ffffff;
    --magenta: #d2177a;
    --magenta-deep: #ad1d64;
    --magenta-bright: #e50b84;
    --ink: #1e1e1e;
    --caption: #8a8a8a;
    --rule: #9a9a9a;
  }
  * { box-sizing: border-box; margin: 0; padding: 0; }
  html, body { width: 1200px; height: 633px; overflow: hidden; }
  body {
    position: relative;
    background: var(--board);
    font-family: "Ubuntu", sans-serif;
    color: var(--ink);
  }

  /* Name set as plain text with one small circle before it */
  .brand {
    position: absolute;
    display: flex;
    align-items: center;
    gap: 0.22em;
    font-family: "Ubuntu", sans-serif;
    font-weight: 400;
    letter-spacing: 0.01em;
    line-height: 1;
    color: var(--magenta);
    white-space: nowrap;
  }
  .brand::before {
    content: "";
    width: 0.3em;
    height: 0.3em;
    border-radius: 50%;
    background: currentColor;
    flex: none;
  }
  .brand--light { color: var(--white); }

  .contact {
    position: absolute;
    font-size: 4.8px;
    line-height: 5.2px;
    color: var(--ink);
    white-space: nowrap;
  }
  .contact strong { font-weight: 700; }
  .contact p + p { margin-top: 2.4px; }

  /* Envelope */
  .envelope {
    position: absolute;
    left: 243px; top: 133px; width: 259px; height: 129px;
    background: var(--paper);
    border: 5.5px solid var(--magenta);
    border-image: linear-gradient(90deg, var(--magenta-deep), var(--magenta-bright)) 1;
  }
  .envelope .brand { left: 84px; top: 48px; font-size: 18px; }
  .envelope .sender-rule {
    position: absolute; left: 196px; top: 91px; width: 1px; height: 27px;
    background: var(--magenta);
  }
  .envelope .contact { left: 202px; top: 93px; }

  /* Business card, front */
  .card-front {
    position: absolute;
    left: 115px; top: 309px; width: 107px; height: 69px;
    background: var(--white);
    border: 4px solid var(--magenta);
    border-radius: 0 14px 0 14px;
  }
  .card-front .brand { left: 22px; top: 24px; font-size: 12px; }

  /* Business card, back */
  .card-back {
    position: absolute;
    left: 237px; top: 309px; width: 107px; height: 69px;
    background: var(--white);
    border-radius: 14px 0 14px 0;
    border-bottom: 3px solid var(--magenta);
    overflow: hidden;
  }
  .card-back .brand { left: 9px; top: 12px; font-size: 6.6px; }
  .card-back .person {
    position: absolute; left: 62px; top: 14px;
    font-size: 4.4px; line-height: 5px; white-space: nowrap;
  }
  .card-back .person .name { font-weight: 700; font-size: 4.8px; }
  .card-back .person .role { color: var(--magenta); }
  .card-back .person .underline {
    width: 33px; height: 0.6px; background: var(--magenta); margin-top: 1px;
  }
  .card-back .company {
    position: absolute; left: 4px; top: 43px; width: 44px;
    font-size: 3px; line-height: 3.6px; text-align: center; white-space: nowrap;
  }
  .card-back .company strong { font-size: 3.8px; }
  .card-back .lines {
    position: absolute; left: 62px; top: 37px;
    font-size: 2.7px; line-height: 3.1px; white-space: nowrap;
  }
  .card-back .lines p + p { margin-top: 1.6px; }

  /* Notebook cover */
  .notebook {
    position: absolute;
    left: 366px; top: 300px; width: 130px; height: 184px;
    background: linear-gradient(90deg, var(--magenta-deep), var(--magenta-bright));
  }
  .notebook .brand { left: 20px; top: 57px; font-size: 18px; }
  .notebook .web {
    position: absolute; left: 0; right: 0; bottom: 12px;
    text-align: center; font-size: 3.6px; color: var(--white);
  }

  /* Letterhead */
  .letterhead {
    position: absolute;
    left: 531px; top: 133px; width: 245px; height: 347px;
    background: var(--paper);
  }
  .letterhead .brand { left: 20px; top: 30px; font-size: 19px; }
  .letterhead .head-rule {
    position: absolute; left: 0; top: 54px; width: 89px; height: 1px;
    background: var(--magenta);
  }
  .letterhead .foot-rule {
    position: absolute; left: 167px; top: 269px; width: 78px; height: 1px;
    background: var(--magenta);
  }
  .letterhead .contact { left: 167px; top: 279px; }

  /* Presentation folder */
  .folder {
    position: absolute;
    left: 808px; top: 132px; width: 254px; height: 366px;
    background: linear-gradient(90deg, var(--magenta-deep), var(--magenta-bright));
  }
  .folder .brand { left: 29px; top: 48px; font-size: 40px; }
  .folder .web {
    position: absolute; left: 0; right: 0; bottom: 26px;
    text-align: center; font-size: 6.4px; color: var(--white);
  }

  /* Caption band */
  .caption-band {
    position: absolute; left: 0; top: 561px; width: 1200px; height: 72px;
    background: var(--white);
  }
  .caption-band .rule {
    position: absolute; top: 33px; height: 1px; background: var(--rule);
  }
  .caption-band .rule--left { left: 0; width: 158px; }
  .caption-band .rule--right { left: 1038px; width: 162px; }
  .caption-band h1 {
    position: absolute; left: 0; right: 0; top: 15px;
    text-align: center;
    font-family: "Open Sans", sans-serif;
    font-weight: 300;
    font-size: 34px;
    letter-spacing: 0.24em;
    line-height: 1;
    color: var(--caption);
    padding-left: 0.24em;
  }
</style>
</head>
<body>

  <section class="envelope" aria-label="Envelope">
    <div class="brand">Lumerova</div>
    <div class="sender-rule"></div>
    <div class="contact">
      <p><strong>Lumerova GmbH</strong><br>Street name 1<br>9999 City name<br>Switzerland</p>
    </div>
  </section>

  <section class="card-front" aria-label="Business card, front">
    <div class="brand">Lumerova</div>
  </section>

  <section class="card-back" aria-label="Business card, back">
    <div class="brand">Lumerova</div>
    <div class="person">
      <div class="name">Name Surname</div>
      <div class="role">PhD</div>
      <div class="role">Managing Partner</div>
      <div class="underline"></div>
    </div>
    <div class="company">
      <strong>Lumerova GmbH</strong><br>Street name 1<br>9999 City name<br>Switzerland
    </div>
    <div class="lines">
      <p>O: +41 (0)21 480 72 00<br>P: +41 (0)21 480 72 15<br>M: +41 (0)79 316 58 42<br>F: +41 (0)21 480 72 01</p>
      <p>name.surname@lumerova-trials.ch<br>www.lumerova-trials.ch</p>
    </div>
  </section>

  <section class="notebook" aria-label="Notebook cover">
    <div class="brand brand--light">Lumerova</div>
    <div class="web">www.lumerova-trials.ch</div>
  </section>

  <section class="letterhead" aria-label="Letterhead">
    <div class="brand">Lumerova</div>
    <div class="head-rule"></div>
    <div class="foot-rule"></div>
    <div class="contact">
      <p><strong>Lumerova GmbH</strong><br>Street name 1<br>9999 City name<br>Switzerland</p>
      <p>O: +41 (0)21 480 72 00<br>P: +41 (0)21 480 72 15<br>M: +41 (0)79 316 58 42<br>F: +41 (0)21 480 72 01</p>
      <p>name.surname@lumerova-trials.ch<br>www.lumerova-trials.ch</p>
    </div>
  </section>

  <section class="folder" aria-label="Presentation folder">
    <div class="brand brand--light">Lumerova</div>
    <div class="web">www.lumerova-trials.ch</div>
  </section>

  <footer class="caption-band">
    <div class="rule rule--left"></div>
    <h1>STATIONERY &amp; BUSINESS CARD DESIGN</h1>
    <div class="rule rule--right"></div>
  </footer>

</body>
</html>
```